Falkrin homes and renovations business card design.

Would like some new card designs utilizing my new logo that look professional. I am open to different colors on the logo or utilize the same ones we have. I like the original concept but would like to see some fresh ideas and build on what we have already done.

Target Market(s)

Custom home building industry, Real estate sales, Renovation projects.

Industry/Entity Type

Home Builder

Contact Information for Business Card

Falkrin Homes and Renovations
2871 96th Avenue
Corvale, Northmark
T2R3W8
Home : 403- 718-4063 Cell: 403- 294-5170

My info is : Dax Falkrin, President and CEO
email: falkrinhomes@maildrop-example.net
Website: falkrinhomes-example.com
websit

Requirements
Must have
• Must Use my new logo design. I am open to different colors on the logo or utilize the same ones in the existing design. I can upload the original logo design if needed.

```html
<!DOCTYPE html>
<html lang="en">
<head>
<meta charset="utf-8">
<title>Falkrin Homes and Renovations – Business Card</title>
<link rel="stylesheet" href="https://fonts.googleapis.com/css2?family=Questrial&display=swap">
<style>
  :root {
    --backdrop: #3a2a35;
    --card-white: #ffffff;
    --card-black: #050505;
    --gold: #b8901f;
    --gold-bright: #d9a91c;
    --icon-yellow: #f2c300;
    --icon-glyph: #ffffff;
  }
  * { margin: 0; padding: 0; box-sizing: border-box; }
  html, body {
    width: 1200px;
    height: 800px;
    overflow: hidden;
    background: var(--backdrop);
    font-family: "Questrial", "Century Gothic", sans-serif;
  }
  .canvas {
    position: relative;
    width: 1200px;
    height: 800px;
  }
  .card {
    position: absolute;
    top: 250px;
    width: 525px;
    height: 300px;
    border-radius: 4px;
    box-shadow: 0 10px 30px rgba(0, 0, 0, 0.35);
    overflow: hidden;
  }
  /* Front side */
  .card-front {
    left: 50px;
    background: var(--card-white);
  }
  .person {
    position: absolute;
    top: 36px;
    left: 44px;
    color: var(--gold);
  }
  .person-name {
    font-size: 24px;
    letter-spacing: 0.5px;
    text-transform: uppercase;
  }
  .person-title {
    margin-top: 4px;
    font-size: 15px;
  }
  .contact-list {
    position: absolute;
    right: 30px;
    bottom: 22px;
    list-style: none;
    color: var(--gold);
    font-size: 14px;
    text-align: right;
  }
  .contact-item {
    display: flex;
    align-items: center;
    justify-content: flex-end;
    gap: 12px;
    margin-top: 8px;
  }
  .contact-lines { line-height: 1.35; }
  .contact-icon {
    flex: 0 0 30px;
    width: 30px;
    height: 30px;
  }
  /* Back side */
  .card-back {
    left: 625px;
    background: var(--card-black);
    display: flex;
    align-items: center;
    justify-content: center;
    gap: 16px;
    padding: 0 40px;
  }
  .brand-square {
    flex: 0 0 22px;
    width: 22px;
    height: 22px;
    background: var(--gold-bright);
  }
  .brand-name {
    max-width: 330px;
    color: var(--gold-bright);
    font-size: 26px;
    line-height: 1.3;
    letter-spacing: 1px;
    text-transform: uppercase;
  }
</style>
</head>
<body>
<main class="canvas">

  <section class="card card-front" aria-label="Business card front">
    <div class="person">
      <p class="person-name">Dax Falkrin</p>
      <p class="person-title">President and CEO</p>
    </div>

    <ul class="contact-list">
      <li class="contact-item">
        <span class="contact-lines">403- 718-4063<br>403- 294-5170</span>
        <svg class="contact-icon" viewBox="0 0 30 30" aria-hidden="true">
          <circle cx="15" cy="15" r="15" fill="var(--icon-yellow)"/>
          <path d="M10 8 l3 0 l1.5 4 l-2 1.5 a9 9 0 0 0 4 4 l1.5 -2 l4 1.5 l0 3 a2 2 0 0 1 -2 2 A13 13 0 0 1 8 10 a2 2 0 0 1 2 -2z" fill="var(--icon-glyph)"/>
        </svg>
      </li>
      <li class="contact-item">
        <span class="contact-lines">falkrinhomes@maildrop-example.net</span>
        <svg class="contact-icon" viewBox="0 0 30 30" aria-hidden="true">
          <circle cx="15" cy="15" r="15" fill="var(--icon-yellow)"/>
          <rect x="8" y="10" width="14" height="10" fill="none" stroke="var(--icon-glyph)" stroke-width="1.6"/>
          <path d="M8 10 l7 6 l7 -6" fill="none" stroke="var(--icon-glyph)" stroke-width="1.6"/>
        </svg>
      </li>
      <li class="contact-item">
        <span class="contact-lines">falkrinhomes-example.com</span>
        <svg class="contact-icon" viewBox="0 0 30 30" aria-hidden="true">
          <circle cx="15" cy="15" r="15" fill="var(--icon-yellow)"/>
          <circle cx="15" cy="15" r="7" fill="none" stroke="var(--icon-glyph)" stroke-width="1.6"/>
          <ellipse cx="15" cy="15" rx="3" ry="7" fill="none" stroke="var(--icon-glyph)" stroke-width="1.3"/>
          <line x1="8" y1="15" x2="22" y2="15" stroke="var(--icon-glyph)" stroke-width="1.3"/>
        </svg>
      </li>
      <li class="contact-item">
        <span class="contact-lines">2871 96th Avenue<br>Corvale, Northmark T2R3W8</span>
        <svg class="contact-icon" viewBox="0 0 30 30" aria-hidden="true">
          <circle cx="15" cy="15" r="15" fill="var(--icon-yellow)"/>
          <path d="M7 15 l8 -7 l8 7 h-2.5 v7 h-11 v-7z" fill="var(--icon-glyph)"/>
        </svg>
      </li>
    </ul>
  </section>

  <section class="card card-back" aria-label="Business card back">
    <span class="brand-square" aria-hidden="true"></span>
    <p class="brand-name">Falkrin Homes and Renovations</p>
  </section>

</main>
</body>
</html>
```